Business Cards for company that supports physicians that do medical research

Need to create a business card for Qorvel Studies (www.qorvelstudies.example), a company devoted to supporting physicians who conduct medical research. The form of the card should match the message of research and information quest. I have provided the logo of the company as an uploaded file. Designs should be simple and slick aimed at very high end clients.

Target Market(s)

Medical doctors that are also researchers

Industry/Entity Type

Medical

Contact Information for Business Card

Should feature logo and fields for personal info:
Name/title
Phone /email

Font styles to use
Serif
Sans Serif

Requirements
Must have
• Qorvel logo and fields for personal info:
• Name: Bertrand Okonfu
• Title: VP Research and Senior Analyst
• Phone: 555-203-4719
• email: info@qorvelstudies.example
Nice to have
• Interesting cards that I've seen:
• 1- all black/charcoal or very dark background
• 2- Plastic - semi-transparent
• 3- non-standard height-width ratios
• 4- Functional cards -- USB drive incorporated
Should not have
• Too busy; needs to stay very simple

```html
<!DOCTYPE html>
<html lang="en">
<head>
<meta charset="utf-8">
<title>Qorvel Studies — Business Card</title>
<link rel="stylesheet" href="https://fonts.googleapis.com/css2?family=Open+Sans:wght@400;600&display=swap">
<style>
  :root {
    --backdrop: #a7a4a4;
    --charcoal: #2b2d31;
    --charcoal-deep: #222428;
    --charcoal-soft: #3a3d42;
    --paper: #ffffff;
    --brand-green: #3aaa48;
    --accent-blue: #3a74b8;
    --name-blue: #2f8fd6;
    --text-light: #e9ebee;
    --text-grey: #5e6166;
  }
  html, body {
    margin: 0;
    width: 1200px;
    height: 1200px;
    overflow: hidden;
    background: var(--backdrop);
    font-family: "Open Sans", Arial, sans-serif;
  }
  .canvas { position: relative; width: 1200px; height: 1200px; }
  .card {
    position: absolute;
    width: 712px;
    height: 416px;
    border-radius: 26px;
    overflow: hidden;
  }
  .card-front { left: 238px; top: 118px; background: var(--charcoal); }
  .card-back { left: 231px; top: 645px; background: var(--charcoal); }
  .photo-area {
    position: absolute; inset: 0;
    background: radial-gradient(ellipse at 75% 40%, var(--charcoal-soft) 0%, var(--charcoal) 55%, var(--charcoal-deep) 100%);
  }
  .wordmark {
    position: absolute;
    left: 0; right: 0;
    text-align: center;
    font-weight: 600;
    letter-spacing: 2px;
    margin: 0;
  }
  .card-front .wordmark {
    top: 178px;
    font-size: 54px;
    color: var(--brand-green);
  }
  .card-back svg.layout { position: absolute; inset: 0; }
  .card-back .wordmark {
    top: 168px;
    left: 36px;
    right: auto;
    width: 260px;
    font-size: 40px;
    line-height: 1.05;
    color: var(--brand-green);
  }
  .contact {
    position: absolute;
    left: 409px;
    top: 124px;
    color: var(--text-light);
  }
  .contact .name {
    margin: 0;
    font-size: 22px;
    font-weight: 600;
    color: var(--name-blue);
    letter-spacing: 0.3px;
  }
  .contact .title {
    margin: 6px 0 0;
    font-size: 16px;
  }
  .contact ul {
    list-style: none;
    margin: 34px 0 0;
    padding: 0;
    font-size: 17.5px;
  }
  .contact li {
    display: flex;
    align-items: center;
    height: 26.5px;
  }
  .contact li svg { width: 16px; height: 16px; margin-right: 12px; fill: var(--name-blue); }
</style>
</head>
<body>
<main class="canvas">

  <section class="card card-front">
    <div class="photo-area" role="img" aria-label="Darkened photograph of a stethoscope resting on a desk"></div>
    <p class="wordmark">Qorvel Studies</p>
  </section>

  <section class="card card-back">
    <div class="photo-area" role="img" aria-label="Darkened photograph of a stethoscope on a keyboard"></div>
    <svg class="layout" viewBox="0 0 712 416" aria-hidden="true">
      <path d="M0 0 H268 C350 90 375 270 288 416 H0 Z" fill="var(--paper)"/>
      <path d="M272 -2 C340 70 370 200 348 300" fill="none" stroke="var(--accent-blue)" stroke-width="7" stroke-linecap="round"/>
    </svg>
    <p class="wordmark">Qorvel Studies</p>
    <div class="contact">
      <h1 class="name">Bertrand Okonfu</h1>
      <p class="title">VP Research &amp; Senior Analyst</p>
      <ul>
        <li><svg viewBox="0 0 16 16"><path d="M2 6c0-2 2-3 6-3s6 1 6 3v1h-3V5.5H5V7H2z M4 8h8l1 5H3z"/></svg>555-203-4719</li>
        <li><svg viewBox="0 0 16 16"><path d="M1 3h14v10H1z M2 4l6 5 6-5" stroke="var(--charcoal)" stroke-width="1"/></svg>info@qorvelstudies.example</li>
        <li><svg viewBox="0 0 16 16"><circle cx="8" cy="8" r="7"/><path d="M1 8h14M8 1v14M3 4h10M3 12h10" stroke="var(--charcoal)" stroke-width="1" fill="none"/></svg>www.qorvelstudies.example</li>
      </ul>
    </div>
  </section>

</main>
</body>
</html>
```